Seeking for catalogue design -for Event Mgmt company

Need to be creative and striking and images to be more enhanced.
The items in the catalogue have to be layout well and easy to read.
Cover and background of catalogue needs to be striking but not overpowering the items.
Catologue needs to be able to put up on website and able to read on mobile.
Font used must be easily readable and not too small.

Target Market(s)

Business and Public Sectors

Industry/Entity Type

Event Planning

Colors

Designer to choose colors to be used in the design.

Requirements
Must have
• Not too many colors but must be creative
Nice to have
• See that the images of items in catalogue have better layout
Should not have
• Not to be so messy

```html
<!DOCTYPE html>
<html lang="en">
<head>
<meta charset="utf-8">
<title>Tarrow Events – Large Inflatable Game Stalls</title>
<link rel="stylesheet" href="https://fonts.googleapis.com/css2?family=Open+Sans:wght@300;400;600;700&family=Cinzel:wght@500&display=swap">
<style>
  :root{
    --teal-light:#abe5e1;
    --teal-mid:#7ccfcf;
    --teal-deep:#6cc3c7;
    --ink:#3a3a3a;
    --title:#3f4547;
    --frame:#7d7d7d;
    --badge:#8f8a87;
    --white:#ffffff;
  }
  html,body{margin:0;padding:0;overflow:hidden;}
  .page{position:relative;width:848px;height:1200px;overflow:hidden;background:var(--white);font-family:"Open Sans",sans-serif;color:var(--ink);}
  .backdrop{position:absolute;inset:0;}
  .brand{position:absolute;left:0;top:0;width:197px;height:64px;background:var(--badge);box-shadow:3px 3px 5px rgba(0,0,0,.35);color:var(--white);text-align:center;}
  .brand-name{font-family:"Open Sans",sans-serif;font-weight:400;font-size:30px;letter-spacing:1px;line-height:1;margin-top:10px;}
  .brand-sub{font-family:"Open Sans",sans-serif;font-weight:400;font-size:8px;letter-spacing:.8px;margin-top:5px;}
  .page-no{position:absolute;right:6px;top:4px;font-size:38px;font-weight:700;color:var(--white);line-height:1.1;}
  .stall{position:absolute;width:280px;text-align:center;}
  .stall-title{font-size:13.5px;font-weight:600;letter-spacing:.6px;color:var(--title);margin:0;white-space:nowrap;}
  .stall-photo{position:absolute;border:4px solid var(--frame);box-shadow:4px 5px 6px rgba(0,0,0,.3);box-sizing:border-box;}
  .stall-info{position:absolute;left:0;width:280px;font-size:15.5px;font-weight:400;line-height:19px;margin:0;color:var(--ink);}
  .notes{position:absolute;left:0;top:1127px;width:848px;height:73px;border-top:1px solid #4d8e93;}
  .notes p{margin:0 0 0 24px;font-size:14.5px;font-weight:700;letter-spacing:.4px;line-height:18.5px;color:#2f3b3d;}
  .notes p:first-child{margin-top:9px;}
</style>
</head>
<body>
<div class="page">
  <svg class="backdrop" width="848" height="1200" viewBox="0 0 848 1200" aria-hidden="true">
    <circle cx="330" cy="1000" r="680" fill="var(--teal-light)"/>
    <circle cx="380" cy="1130" r="640" fill="var(--teal-deep)"/>
    <circle cx="905" cy="25" r="355" fill="var(--teal-light)"/>
    <circle cx="935" cy="20" r="325" fill="var(--teal-deep)"/>
  </svg>

  <div class="brand">
    <div class="brand-name">TARROW</div>
    <div class="brand-sub">TARROW EVENTS PTE LTD</div>
  </div>
  <div class="page-no">07</div>

  <!-- Row 1 -->
  <div class="stall" style="left:0;top:76px;">
    <h2 class="stall-title">LARGE INFLATABLE GAME STALL</h2>
    <div class="stall-photo" role="img" aria-label="Photo of the large inflatable archery game" style="left:45px;top:29px;width:174px;height:168px;background:linear-gradient(160deg,#e8342a,#f7d320 55%,#2a6fd1);"></div>
    <p class="stall-info" style="top:223px;left:-7px;">Large Inflatable Archery Game<br>3.5m by 2.4m by 2.7m (H)<br>$540/stall<br>Require 1x Powerpoint (680W)<br>Subsequent day: $220</p>
  </div>
  <div class="stall" style="left:294px;top:76px;">
    <h2 class="stall-title">LARGE INFLATABLE GAME STALL</h2>
    <div class="stall-photo" role="img" aria-label="Photo of the large inflatable soccer goal" style="left:52px;top:26px;width:174px;height:168px;background:linear-gradient(160deg,#d9262a,#f0a0a8 50%,#d9262a);"></div>
    <p class="stall-info" style="top:218px;">Large Inflatable Soccer<br>3.5m by 2.4m by 2.4m (H)<br>$540/stall<br>Require 1x Powerpoint (680W)<br>Subsequent day: $220</p>
  </div>
  <div class="stall" style="left:577px;top:76px;">
    <h2 class="stall-title">LARGE INFLATABLE GAME STALL</h2>
    <div class="stall-photo" role="img" aria-label="Photo of the large plinko game" style="left:63px;top:28px;width:174px;height:168px;background:linear-gradient(180deg,#e9eeee,#d94a3a 30%,#2f62c8 60%,#e9eeee);"></div>
    <p class="stall-info" style="top:218px;left:8px;">Large Plinko Game<br>2.5m by 2.4m by 4m (H)<br>$540/stall<br>Require 1x Powerpoint (950W)<br>Subsequent day: $220</p>
  </div>

  <!-- Row 2 -->
  <div class="stall" style="left:4px;top:428px;">
    <h2 class="stall-title">LARGE INFLATABLE GAME STALL</h2>
    <div class="stall-photo" role="img" aria-label="Photo of the 3 in 1 sports game inflatable" style="left:41px;top:31px;width:174px;height:168px;background:linear-gradient(170deg,#e43a2a,#2d8fe0 40%,#3cb34a 75%,#e43a2a);"></div>
    <p class="stall-info" style="top:221px;left:-19px;">3 in 1 Sports Game<br>3.5m by 2.4m by 3m<br>$780/stall<br>Require 1x Powerpoint (1500W)<br>Subsequent day: $320</p>
  </div>
  <div class="stall" style="left:301px;top:428px;">
    <h2 class="stall-title">LARGE INFLATABLE GAME STALL</h2>
    <div class="stall-photo" role="img" aria-label="Photo of the 4 in 1 sports games inflatable arches" style="left:47px;top:31px;width:174px;height:168px;background:linear-gradient(170deg,#e9e6e2,#d9262a 45%,#3cae4a 75%,#ddd8d2);"></div>
    <p class="stall-info" style="top:218px;left:-4px;">4 in 1 Sports Games<br>7m by 4m by 2.6m (H)<br>$780/stall<br>Require 1x Powerpoint (1500W)<br>Subsequent day: $220</p>
  </div>
  <div class="stall" style="left:577px;top:428px;">
    <h2 class="stall-title">LARGE INFLATABLE GAME STALL</h2>
    <div class="stall-photo" role="img" aria-label="Photo of the axe throw inflatable" style="left:66px;top:31px;width:174px;height:168px;background:linear-gradient(175deg,#5a5a5a,#b43a32 40%,#7a6a5a 70%,#2e7a3a);"></div>
    <p class="stall-info" style="top:221px;left:0;">Axe Throw Inflatable<br>2.7m by 3.5m by 2.7m<br>$600/stall<br>Require 1x Powerpoint (1500W)<br>Subsequent day: $220</p>
  </div>

  <!-- Row 3 -->
  <div class="stall" style="left:6px;top:781px;">
    <h2 class="stall-title">LARGE INFLATABLE GAME STALL</h2>
    <div class="stall-photo" role="img" aria-label="Photo of the colosseum warrior inflatable arena" style="left:37px;top:28px;width:174px;height:168px;background:linear-gradient(170deg,#7a7a7a,#f5b81c 30%,#f08a1a 70%,#3cae4a);"></div>
    <p class="stall-info" style="top:228px;left:-18px;">Colosseum Warrior<br>5.5m x 5.5m x 3.5m<br>2 participant at a time<br>Require 1x Powerpoint (1100W)<br>SGD$780</p>
  </div>
  <div class="stall" style="left:303px;top:783px;">
    <h2 class="stall-title">LARGE INFLATABLE GAME STALL</h2>
    <div class="stall-photo" role="img" aria-label="Photo of the human whack a mole inflatable ring" style="left:51px;top:28px;width:174px;height:168px;background:radial-gradient(circle at 50% 45%,#f5c21c 10%,#2f7fe0 35%,#e43a2a 65%,#f08a1a);"></div>
    <p class="stall-info" style="top:226px;left:-14px;">Human Whack a Mole<br>5m x 5m x 1.8m<br>up to 7 participants at a time<br>Require 1x Powerpoint (1100W)<br>SGD$780</p>
  </div>
  <div class="stall" style="left:577px;top:783px;">
    <h2 class="stall-title">LARGE INFLATABLE GAME STALL</h2>
    <div class="stall-photo" role="img" aria-label="Photo of the sticky wall inflatable" style="left:80px;top:22px;width:141px;height:190px;background:linear-gradient(100deg,#e43a2a,#f5d21c 45%,#2f5fd0 80%,#d9ecef);"></div>
    <p class="stall-info" style="top:221px;left:-4px;">Sticky Wall<br>5.5m by 2.4m by 2.8m (H)<br>1 participant at a time<br>Require 1x Powerpoint (1100W)<br>SGD$960</p>
  </div>

  <footer class="notes">
    <p>*Size stated above is estimated only.</p>
    <p>*Rates include Delivery, Set up, Dismantle and Collection of the equipments.</p>
    <p>*The more items or more days rented, we may be able to quote a much better discounted package rate</p>
  </footer>
</div>
</body>
</html>
```